New design for existing catalog pages

We want to update and improve our existing design. The existing products on the designs should be adopted. Also the prices, descriptions and article numbers.
It is important that we receive an Indesign file that we can adapt. Also replace the images and adjust texts and prices.

Target Market(s)

Older people with high incomes. More conservative people.

Industry/Entity Type

Münzen und Briefmarkenhandel

Requirements
Must have
• Noble, simple and timeless design that looks high quality.
Nice to have
• The expensive products should be presented accordingly
Should not have
• Don't look cheap. Not too many different and bright colors

```html
<!DOCTYPE html>
<html lang="de">
<head>
<meta charset="utf-8">
<title>Katalog – Top Münz-Raritäten / Helvetische Republik</title>
<link rel="stylesheet" href="https://fonts.googleapis.com/css2?family=EB+Garamond:wght@400;500&family=Montserrat:wght@400;500;600&display=swap">
<style>
:root{
  --backdrop:#3c3d40;
  --paper:#ffffff;
  --royal:#213f94;
  --navy:#0f1a5a;
  --title-blue:#2b4a9a;
  --ink:#1c1c1c;
  --gold-rule:#b39a62;
  --gold-dot:#b89550;
  --badge:#1a1a1a;
  --white:#ffffff;
}
*{margin:0;padding:0;box-sizing:border-box}
html,body{width:1200px;height:849px;overflow:hidden;background:var(--backdrop)}
.spread{position:relative;width:1200px;height:849px}
.page{position:absolute;top:25px;width:566px;height:800px;overflow:hidden}
.page-left{left:28px;background:var(--paper)}
.page-right{left:603px;background:var(--royal)}
.band{position:absolute;left:0;width:100%}
.band-blue{background:var(--royal)}
.band-navy{background:var(--navy)}
.serif{font-family:"EB Garamond",Georgia,serif;font-weight:500}
.page-title{position:absolute;left:35px;top:28px;font-size:21px;color:var(--title-blue)}
.page-right .page-title{color:var(--white)}
.rule{position:absolute;left:35px;width:496px;height:1px;background:var(--gold-rule)}
.item-title{position:absolute;left:35px;font-size:16px;color:var(--ink)}
.on-blue{color:var(--white)}
.text-column{position:absolute;left:35px;width:182px;font-family:"Montserrat",Arial,sans-serif;color:var(--ink)}
.body-copy{font-size:7.9px;line-height:12.4px;text-align:justify;font-weight:400;letter-spacing:-.05px;hyphens:auto}
.body-copy.left{text-align:left}
.text-column.on-blue{color:var(--white)}
.specs{list-style:none;margin-top:3px;font-size:8.1px;line-height:12.4px;font-weight:500;white-space:nowrap}
.specs li::before{content:"•";color:var(--gold-dot);margin-right:4px}
.price{position:absolute;font-family:"Montserrat",Arial,sans-serif;font-weight:600;font-size:10.5px;color:var(--ink);white-space:nowrap;word-spacing:3px}
.price.on-blue{color:var(--white)}
.coin{position:absolute;border-radius:50%;box-shadow:2px 3px 6px rgba(0,0,0,.35)}
.coin-gold{background:radial-gradient(circle at 40% 35%,#f4dc8a,#d9ad45 55%,#a77a22)}
.coin-pale{background:radial-gradient(circle at 40% 35%,#fbf0cf,#e5cf94 55%,#b89b5c)}
.coin-bright{background:radial-gradient(circle at 40% 35%,#fbe37a,#e6b830 55%,#b98a18)}
.badge{position:absolute;background:var(--badge);color:var(--white);font-family:"Montserrat",Arial,sans-serif;font-weight:600;display:flex;align-items:center;justify-content:center;border-radius:10px 2px 10px 2px;box-shadow:0 0 0 1.5px #8a7440,2px 2px 4px rgba(0,0,0,.4);letter-spacing:.3px}
.footer{position:absolute;left:0;top:765px;width:100%;height:35px;font-family:"Montserrat",Arial,sans-serif;font-size:10.5px;color:var(--white);font-weight:500}
.footer .label{position:absolute;left:35px;top:8px}
.footer .folio{position:absolute;right:35px;top:8px}
.intro{position:absolute;left:35px;top:108px;width:496px;font-family:"Montserrat",Arial,sans-serif;font-size:8.1px;line-height:12.6px;color:var(--white);text-align:justify;font-weight:500;letter-spacing:-.05px;hyphens:auto}
.intro p{margin-bottom:5px}
.checklist{position:absolute;left:344px;top:609px;list-style:none;font-family:"Montserrat",Arial,sans-serif;font-size:9.4px;line-height:18.3px;color:var(--white)}
.checklist li{display:flex;align-items:center}
.checklist svg{margin-right:8px}
.order-table{position:absolute;left:35px;top:719px;font-family:"Montserrat",Arial,sans-serif;font-size:10px;font-weight:600;color:var(--white);border-collapse:collapse;table-layout:fixed}
.order-table td{padding:0 0 6px 0;white-space:nowrap}
.order-table td.art{width:93px}
.order-table td.desc{width:273px;font-weight:500}
.deco{position:absolute;left:0;top:0}
</style>
</head>
<body>
<div class="spread">

  <section class="page page-left" lang="de">
    <div class="band band-blue" style="top:297px;height:239px"></div>
    <div class="band band-blue" style="top:765px;height:35px"></div>

    <h1 class="page-title serif">Top Münz-Raritäten</h1>
    <div class="rule" style="top:64px"></div>

    <h2 class="item-title serif" style="top:76px">20 Franken 1873, 3-Punkt - Probeprägung</h2>
    <div class="text-column" style="top:101px">
      <p class="body-copy">873 liess das Finanzdepartement vom bekannten Graveur Anton Berger in seiner Prägestätte in Brüssel ein Stempelpaar und 1‘000 Exemplare einer neuen Eidgenössischen Goldmünze anfertigen. Der oberste der drei Punkte beinhaltete das Münzzeichen des Graveurs und stellte einen Engelskopf dar, der jedoch bei oberflächlicher Betrachtung als Punkt wahrgenommen wird.</p>
      <ul class="specs">
        <li>Schweiz - 16 / 32 Franken</li>
        <li>1800, Helvetische Republik</li>
        <li>23 mm / 29 mm Durchmesser</li>
        <li>7,65 Gramm / 15,26 Gramm - Gold</li>
        <li>vorzüglich bis unzirkuliert</li>
      </ul>
    </div>
    <div class="coin coin-gold" role="img" aria-label="Goldmünze 20 Franken 1873, Wertseite mit Kranz" style="left:227px;top:117px;width:156px;height:156px"></div>
    <div class="coin coin-gold" role="img" aria-label="Goldmünze 20 Franken 1873, Bildseite mit sitzender Helvetia" style="left:362px;top:74px;width:178px;height:178px"></div>
    <div class="price" style="left:375px;top:270px">7870.1873.01 &nbsp;9995,– CHF</div>

    <h2 class="item-title serif on-blue" style="top:308px">Das 100 Franken Vreneli von 1925</h2>
    <div class="text-column on-blue" style="top:333px">
      <p class="body-copy">1925, 100 Fr. Gold- Vreneli, bis unzirkuliert, mit Stempelglanz, Top-Erhaltung, Durchmesser: 35mm, Motiv: Helvetiakopf (Vreneli), Entwurf: Paul Emile Roth, Neuchâtel, Münzzeichen B, Auflage: 5’000.</p>
    </div>
    <div class="price on-blue" style="left:35px;top:467px">7874.1925.08 &nbsp;25900,– CHF</div>
    <div class="coin coin-pale" role="img" aria-label="Goldmünze 100 Franken 1925, Wertseite" style="left:208px;top:343px;width:184px;height:184px"></div>
    <div class="coin coin-pale" role="img" aria-label="Goldmünze 100 Franken 1925, Bildseite mit Frauenkopf" style="left:361px;top:289px;width:182px;height:182px"></div>
    <div class="badge" style="left:370px;top:482px;width:155px;height:25px;font-size:15px">TOP - RARITÄT</div>

    <h2 class="item-title serif" style="top:547px">Das 100 Franken Vreneli von 1925</h2>
    <div class="text-column" style="top:572px">
      <p class="body-copy left">925, 100 Fr. Gold- Vreneli, fast FDC, Top-Erhaltung, Durchmesser: 35mm, Motiv: Helvetiakopf (Vreneli),<br>Entwurf: Paul Emile Roth, Neuchâtel,<br>Münzzeichen B, Auflage: 5’000</p>
    </div>
    <div class="price" style="left:35px;top:705px">7874.1925.07 &nbsp;25900,– CHF</div>
    <div class="coin coin-pale" role="img" aria-label="Goldmünze 100 Franken 1925 in Top-Qualität, Wertseite" style="left:207px;top:579px;width:178px;height:178px"></div>
    <div class="coin coin-pale" role="img" aria-label="Goldmünze 100 Franken 1925 in Top-Qualität, Bildseite" style="left:363px;top:531px;width:180px;height:180px"></div>
    <div class="badge" style="left:368px;top:716px;width:154px;height:25px;font-size:15px">TOP - QUALITÄT</div>

    <div class="footer">
      <span class="label">Top Münz-Raritäten</span>
      <span class="folio">13</span>
    </div>
  </section>

  <section class="page page-right" lang="de">
    <div class="band band-navy" style="top:593px;height:207px"></div>
    <svg class="deco" width="566" height="800" viewBox="0 0 566 800" aria-hidden="true">
      <circle cx="286" cy="576" r="290" fill="none" stroke="#8fa3d8" stroke-width=".7" stroke-dasharray="1.5 2.5" opacity=".6"/>
    </svg>

    <h1 class="page-title serif">Helvetische Republik - Duplonen</h1>
    <div class="rule" style="top:64px"></div>
    <h2 class="item-title serif on-blue" style="top:76px">Duplone und Doppelduplone der Helvetischen Republik 1798 - 1803</h2>

    <div class="intro">
      <p>Helvetische Republik ist die offizielle Bezeichnung des schweizerischen Staatswesens, das am 12. April 1798 die alte Eidgenossenschaft ablöste und bis zum 10. März 1803 bestand.</p>
      <p>Frankreich nutzte die bestehende Unzufriedenheit der ländlichen Eliten in den Untertanengebieten der alten Eidgenossenschaft, sowie der aufgeklärten Bürger in den städtischen Orten und förderte gezielt revolutionäre Bestrebungen. Angefacht oder ausgelöst und zugleich auch abgesichert wurde die Umwälzung durch französische Truppen, die ab Ende Januar in einer Zangenbewegung von der Waadt und vom Jura her in das westliche Mittelland vorstiessen (Franzoseneinfall). In den Kampfhandlungen Anfang März 1798 ging die alte Eidgenossenschaft unter.</p>
      <p>Einige Städte, allen voran Bern, hatten beträchtliche Vermögen in ihren Schatzkammern. Der sogenannte Staatsschatz von Bern wurde von den Französischen Truppen geplündert. Mehrere Kutschen mit Gold und Silber, sowie die Bären aus dem Bärengraben, wurden nach Paris gekarrt.</p>
      <p>Mit der Einführung der Helvetischen Republik ging das Münzwesen von den Kantonen auf den Zentralstaat über und der Franken wurde als Währung festgelegt. In dieser Zeit entstanden die Duplonen (16 Franken) und Doppelduplonen (32 Franken) der Helvetischen Republik.</p>
    </div>

    <div class="coin coin-bright" role="img" aria-label="Goldmünze Helvetische Republik, Bildseite mit stehendem Bannerträger" style="left:142px;top:298px;width:226px;height:226px"></div>
    <div class="coin coin-bright" role="img" aria-label="Doppelduplone 32 Franken 1800, Wertseite mit Kranz" style="left:21px;top:448px;width:256px;height:256px"></div>
    <div class="coin coin-pale" role="img" aria-label="Duplone 16 Franken 1800, Wertseite mit Kranz" style="left:313px;top:411px;width:164px;height:164px"></div>
    <div class="badge" style="left:27px;top:371px;width:127px;height:21px;font-size:12.5px">TOP - RARITÄT</div>
    <div class="badge" style="left:170px;top:672px;width:129px;height:21px;font-size:12.5px">DUPLONENPAAR</div>

    <ul class="checklist">
      <li><svg width="12" height="12" viewBox="0 0 12 12"><path d="M1 6.5 L4.5 10 L11 1" fill="none" stroke="#b39a62" stroke-width="1.8"/></svg>Schweiz - 16 / 32 Franken</li>
      <li><svg width="12" height="12" viewBox="0 0 12 12"><path d="M1 6.5 L4.5 10 L11 1" fill="none" stroke="#b39a62" stroke-width="1.8"/></svg>1800, Helvetische Republik</li>
      <li><svg width="12" height="12" viewBox="0 0 12 12"><path d="M1 6.5 L4.5 10 L11 1" fill="none" stroke="#b39a62" stroke-width="1.8"/></svg>23 mm / 29 mm Durchmesser</li>
      <li><svg width="12" height="12" viewBox="0 0 12 12"><path d="M1 6.5 L4.5 10 L11 1" fill="none" stroke="#b39a62" stroke-width="1.8"/></svg>7,65 Gramm / 15,26 Gramm - Gold</li>
      <li><svg width="12" height="12" viewBox="0 0 12 12"><path d="M1 6.5 L4.5 10 L11 1" fill="none" stroke="#b39a62" stroke-width="1.8"/></svg>vorzüglich bis unzirkuliert</li>
    </ul>

    <table class="order-table">
      <tr><td class="art">7997.1800.015</td><td class="desc">Helvetische Republik - Duplone 16 Franken</td><td>9500,– CHF</td></tr>
      <tr><td class="art">7997.1800.025</td><td class="desc">Helvetische Republik - Doppelduplone 32 Franken</td><td>28900,– CHF</td></tr>
    </table>

    <div class="rule" style="top:765px;background:#7f8fc2"></div>
    <div class="footer">
      <span class="label">Helvetische Republik - Duplonen</span>
      <span class="folio">15</span>
    </div>
  </section>

</div>
</body>
</html>
```